Hartwell Estates Business Cards

I would like a business card that includes myself and my partner.
Includes: Logo, office #, email, website, our names, our numbers and possibly the address. I would also like the logo to be embossed and the card to be horizontal.
There is a photo of our yard signs to give you an idea of the colors of our business.

Target Market(s)

Everyone in real estate market.
We are in a rural area. Our clientele are from all socioeconomic backgrounds.

Industry/Entity Type

Real Estate Agent

Contact Information for Business Card

Company Name: Hartwell Estates
Our Names, Titles & Cell #'s : Dana Pembrook-Broker (555).317.6624, Marla Pembrook-Realtor (555).609.1385
Office #: (555).240.3918
Website: hartwellestates-demo.com
Joint Email: pembrook@hartwellestates-demo.com
Office Address: 418B W. Calloway Ave.
Linwood, LA. 70913

Font styles to use
Serif

Requirements
Must have
• HORIZONTAL, Logo, Myself and my partners names, Our cell #'s, our office #, our website, our email address
Nice to have
• Embossed logo, office address, our titles.

```html
<!DOCTYPE html>
<html lang="en">
<head>
<meta charset="utf-8">
<title>Hartwell Estates Business Cards</title>
<link rel="stylesheet" href="https://fonts.googleapis.com/css2?family=Libre+Baskerville:wght@700&family=Source+Sans+3:wght@400;600;700&display=swap">
<style>
  :root {
    --brand-purple: #4a2866;
    --ink-grey: #4a4a4a;
    --paper: #ffffff;
    --backdrop: #e9e7ec;
  }
  * { margin: 0; padding: 0; box-sizing: border-box; }
  html, body { width: 1200px; height: 900px; overflow: hidden; }
  body {
    background: var(--backdrop);
    font-family: "Source Sans 3", "Segoe UI", sans-serif;
    position: relative;
  }
  .card {
    position: absolute;
    left: 300px;
    width: 600px;
    height: 343px;
    overflow: hidden;
    box-shadow: 0 2px 10px rgba(0,0,0,0.12);
  }
  .card--front { top: 88px; background: var(--brand-purple); color: var(--paper); }
  .card--back { top: 470px; background: var(--paper); color: var(--ink-grey); }

  .wordmark {
    position: absolute;
    font-family: "Libre Baskerville", Georgia, serif;
    font-weight: 700;
    display: flex;
    align-items: center;
    gap: 16px;
  }
  .wordmark__dot { width: 46px; height: 46px; border-radius: 50%; flex: none; }
  .wordmark__text { display: flex; flex-direction: column; align-items: flex-end; }
  .wordmark__name { font-size: 40px; letter-spacing: 1px; line-height: 1; }
  .wordmark__rule { width: 100%; height: 2px; margin: 7px 0 5px; }
  .wordmark__sub { font-size: 25px; line-height: 1; padding-right: 44px; }

  .card--front .wordmark { left: 96px; top: 100px; color: var(--paper); }
  .card--front .wordmark__dot, .card--front .wordmark__rule { background: var(--paper); }
  .website { position: absolute; left: 178px; top: 268px; font-size: 15px; letter-spacing: 0.2px; }

  .card--back .wordmark { left: 278px; top: 98px; color: var(--brand-purple); }
  .card--back .wordmark__name { font-size: 34px; }
  .card--back .wordmark__sub { font-size: 22px; padding-right: 36px; }
  .card--back .wordmark__dot, .card--back .wordmark__rule { background: var(--brand-purple); }

  .agents { position: absolute; left: 30px; top: 30px; }
  .agent { margin-bottom: 12px; line-height: 1.15; }
  .agent__name { color: var(--brand-purple); font-weight: 700; font-size: 16px; }
  .agent__title { font-size: 15px; }
  .agent__phone { font-size: 15px; display: flex; align-items: center; gap: 5px; }
  .divider { position: absolute; height: 1.5px; background: var(--brand-purple); }
  .divider--top { left: 30px; top: 188px; width: 230px; }
  .divider--bottom { left: 30px; top: 290px; width: 530px; }
  .office { position: absolute; left: 30px; top: 200px; font-size: 15px; line-height: 1.6; }
  .office__label { color: var(--brand-purple); font-weight: 700; }
  .office__gap { display: inline-block; width: 14px; }
</style>
</head>
<body>
  <section class="card card--front" aria-label="Card front">
    <div class="wordmark">
      <span class="wordmark__dot"></span>
      <div class="wordmark__text">
        <span class="wordmark__name">HARTWELL</span>
        <span class="wordmark__rule"></span>
        <span class="wordmark__sub">Estates</span>
      </div>
    </div>
    <p class="website">www.hartwellestates-demo.com</p>
  </section>

  <section class="card card--back" aria-label="Card back">
    <div class="agents">
      <div class="agent">
        <div class="agent__name">Dana Pembrook</div>
        <div class="agent__title">Broker</div>
        <div class="agent__phone">
          <svg width="8" height="12" viewBox="0 0 8 12" aria-hidden="true"><rect x="0.75" y="0.75" width="6.5" height="10.5" rx="1.2" fill="none" stroke="#4a2866" stroke-width="1.5"/><circle cx="4" cy="9.2" r="0.8" fill="#4a2866"/></svg>
          (555).317.6624
        </div>
      </div>
      <div class="agent">
        <div class="agent__name">Marla Pembrook</div>
        <div class="agent__title">Realtor</div>
        <div class="agent__phone">
          <svg width="8" height="12" viewBox="0 0 8 12" aria-hidden="true"><rect x="0.75" y="0.75" width="6.5" height="10.5" rx="1.2" fill="none" stroke="#4a2866" stroke-width="1.5"/><circle cx="4" cy="9.2" r="0.8" fill="#4a2866"/></svg>
          (555).609.1385
        </div>
      </div>
    </div>
    <div class="divider divider--top"></div>
    <div class="office">
      <div>418B W. Calloway Ave. Linwood, LA. 70913</div>
      <div><span class="office__label">M:</span> (555).240.3918<span class="office__gap"></span><span class="office__label">E:</span> pembrook@hartwellestates-demo.com</div>
    </div>
    <div class="divider divider--bottom"></div>
    <div class="wordmark">
      <span class="wordmark__dot"></span>
      <div class="wordmark__text">
        <span class="wordmark__name">HARTWELL</span>
        <span class="wordmark__rule"></span>
        <span class="wordmark__sub">Estates</span>
      </div>
    </div>
  </section>
</body>
</html>
```